Website for Torvel Capital - investment banking firm

We have a corporate identity (thanks to Ravinka/31842) and want to extend that into a website design.  See the attached zipped files.
We have software folks in-house to do the coding.
See the attached Project Brief & Notes for more details.  Don't worry about the actual text - lorem ipsum will be fine.
The server will be Apache.
Thank you!
Desmond

Industry/Entity Type
Investment

```html
<!DOCTYPE html>
<html lang="en">
<head>
<meta charset="utf-8">
<title>Torvel Capital</title>
<link href="https://fonts.googleapis.com/css2?family=Lato:ital,wght@0,400;0,700;1,400&family=Tinos:wght@400;700&display=swap" rel="stylesheet">
<style>
:root{
  --blue:#1f4e8c;
  --blue-dark:#173f73;
  --ink:#1d1d1d;
  --text:#333;
  --grey-line:#c9cccc;
  --page:#f1f3f2;
  --hero-a:#e3e9e9;
  --hero-b:#9fb0b0;
  --white:#fff;
}
*{margin:0;padding:0;box-sizing:border-box}
html,body{width:1200px;height:971px;overflow:hidden}
body{position:relative;background:var(--page);font-family:'Lato',sans-serif;color:var(--text)}
.abs{position:absolute}
.site-header{position:absolute;left:0;top:0;width:1200px;height:94px;background:#f3f5f5}
.brand{left:132px;top:22px;display:flex;align-items:center;gap:12px}
.brand-mark{width:44px;height:44px;background:var(--blue)}
.brand-name{font-family:'Lato',sans-serif;font-size:34px;font-weight:400;color:var(--blue);letter-spacing:1px}
.top-contact{top:10px;display:flex;align-items:center;gap:6px;color:var(--blue)}
.top-contact.email{left:719px;font-size:13px;font-weight:700}
.top-contact.phone{left:901px;font-size:19px;font-weight:700}
.main-nav{left:498px;top:57px;display:flex;align-items:center;font-size:14px;color:var(--ink)}
.main-nav span{padding:0 13px;border-left:1px solid #9aa8b8;line-height:17px}
.main-nav span.active{background:var(--blue);color:var(--white);border:none;line-height:26px;padding:0 17px}
.main-nav span.active+span{border-left:none}
.hero{left:0;top:94px;width:1200px;height:474px;background:radial-gradient(ellipse at 50% 60%,var(--hero-a) 0%,#c3cfcf 45%,var(--hero-b) 100%)}
.hero-title{left:0;top:128px;width:1200px;text-align:center;font-family:'Tinos',serif;font-size:29px;line-height:42px;color:var(--white)}
.hero-title strong{color:var(--blue);text-transform:uppercase}
.hero-art{left:255px;top:225px;width:690px;height:300px;background:radial-gradient(ellipse at 50% 60%,#f4f7f7 0%,rgba(220,228,228,.6) 55%,rgba(220,228,228,0) 75%)}
.card{top:527px;width:288px;height:166px;border-radius:8px 8px 0 0;background:linear-gradient(#ffffff 0%,#f6f7f6 45%,rgba(241,243,242,0) 100%)}
.card-title{left:14px;top:8px;display:flex;align-items:center;gap:12px;font-family:'Tinos',serif;font-size:25px;color:var(--ink)}
.card-title i{display:block;width:28px;height:28px;background:var(--blue);border-radius:3px}
.card-title em{font-style:normal;color:var(--blue)}
.card-icon{left:16px;top:54px;width:58px;height:58px;border:2px solid #333;border-radius:50%;display:flex;align-items:center;justify-content:center}
.card-text{left:90px;top:52px;width:186px;font-size:13.5px;line-height:20px;letter-spacing:.6px;color:#222;height:80px;overflow:hidden}
.card-list{left:90px;top:52px;width:190px;list-style:none;font-size:13.5px;line-height:16px;color:#222}
.card-list li{position:relative;padding-left:13px;margin-bottom:7px}
.card-list li:before{content:"";position:absolute;left:0;top:4px;border-left:5px solid #888;border-top:4px solid transparent;border-bottom:4px solid transparent}
.news-head{font-weight:700;letter-spacing:0}
.read-more{left:90px;top:139px;font-size:11.5px;font-weight:700;color:var(--blue)}
.divider{left:170px;top:705px;width:870px;height:1px;background:linear-gradient(90deg,transparent,var(--grey-line) 15%,var(--grey-line) 85%,transparent)}
.testi-title{left:110px;top:730px;width:158px;text-align:right;font-family:'Tinos',serif;font-size:26px;line-height:30px;color:var(--ink)}
.testi-title em{font-style:normal;color:var(--blue)}
.testi-quote{left:339px;top:734px;width:712px;font-style:italic;font-size:14px;line-height:20px;color:#222}
.testi-name{left:339px;top:781px;font-style:italic;font-size:14px;color:var(--blue)}
.site-footer{left:0;top:826px;width:1200px;height:145px;background:var(--blue)}
.foot-h{top:22px;font-size:18px;font-weight:700;color:var(--white);padding-bottom:10px;border-bottom:1px solid #5a7fb0}
.foot-text{color:var(--white);font-size:12.5px;line-height:20px}
.foot-strong{color:var(--white);font-size:14px;font-weight:700}
.email-input{left:555px;top:60px;width:206px;height:28px;background:var(--blue-dark);color:#9fb3cf;font-style:italic;font-size:12px;line-height:28px;padding-left:9px}
.go-btn{left:761px;top:60px;width:38px;height:28px;background:var(--white);color:var(--blue);font-weight:700;font-size:16px;text-align:center;line-height:28px}
.follow{left:554px;top:108px;display:flex;align-items:center;gap:9px;color:var(--white);font-weight:700;font-size:15px}
.follow i{display:block;width:29px;height:29px;border:2px solid var(--white);border-radius:50%}
.foot-badge{left:917px;top:797px;width:107px;height:84px;border-radius:0 0 54px 54px;background:var(--page)}
.copyright{left:870px;top:85px;width:200px;text-align:center;color:var(--white);font-size:13.5px;line-height:20px}
</style>
</head>
<body>
<header class="site-header">
  <div class="abs brand"><span class="brand-mark"></span><span class="brand-name">Torvel Capital</span></div>
  <div class="abs top-contact email">
    <svg width="32" height="24" viewBox="0 0 32 24"><rect x="1" y="1" width="24" height="22" rx="3" fill="none" stroke="#333" stroke-width="1.5"/><path d="M25 10l5 3-5 3" fill="none" stroke="#333" stroke-width="1.5"/><rect x="6" y="7" width="14" height="10" fill="#333"/><path d="M6 7l7 6 7-6" fill="none" stroke="#fff" stroke-width="1.2"/></svg>
    info@torvelcapital.com
  </div>
  <div class="abs top-contact phone">
    <svg width="32" height="24" viewBox="0 0 32 24"><rect x="1" y="1" width="24" height="22" rx="3" fill="none" stroke="#333" stroke-width="1.5"/><path d="M25 10l5 3-5 3" fill="none" stroke="#333" stroke-width="1.5"/><rect x="9" y="5" width="8" height="14" rx="1.5" fill="#333"/><rect x="10.5" y="7" width="5" height="5" fill="#fff"/></svg>
    469-555-0148
  </div>
  <nav class="abs main-nav">
    <span class="active">About</span><span>Services</span><span>Current Engagements</span><span>Completed Transactions</span><span>Contact Us</span>
  </nav>
</header>

<section class="abs hero" role="img" aria-label="Chess scene: a red king standing among rows of pale grey pawns"></section>
<div class="abs hero-art" role="img" aria-label="Chess pieces"></div>
<h1 class="abs hero-title" style="font-weight:400">Private Investment Banking Advisory Firm That Acts As An Intermediary<br>On Behalf Of <strong>Buyers &amp; Sellers of Private Companies.</strong></h1>

<article class="abs card" style="left:134px">
  <h2 class="abs card-title" style="font-weight:400"><i></i><span><em>Who</em> We Are</span></h2>
  <div class="abs card-icon"><svg width="30" height="30" viewBox="0 0 30 30"><circle cx="15" cy="9" r="6" fill="#333"/><path d="M3 28c0-8 5-12 12-12s12 4 12 12z" fill="#333"/></svg></div>
  <p class="abs card-text">Torvel Capital's history in mergers and acquisitions traces back to 1998. We pride our selves in successfully</p>
  <a class="abs read-more">READ MORE »</a>
</article>

<article class="abs card" style="left:456px">
  <h2 class="abs card-title" style="font-weight:400"><i></i><span><em>What</em> We Do</span></h2>
  <div class="abs card-icon"><svg width="36" height="36" viewBox="0 0 36 36"><circle cx="14" cy="22" r="9" fill="none" stroke="#333" stroke-width="5" stroke-dasharray="4 3"/><circle cx="14" cy="22" r="3" fill="#333"/><circle cx="27" cy="9" r="5" fill="none" stroke="#333" stroke-width="4" stroke-dasharray="3 2"/></svg></div>
  <ul class="abs card-list">
    <li>Buy-Side Acquisitions</li>
    <li>Recapitalizations &amp; Growth Capital Partnerships</li>
    <li>Sell-Side Transactions</li>
  </ul>
  <a class="abs read-more">READ MORE »</a>
</article>

<article class="abs card" style="left:778px">
  <h2 class="abs card-title" style="font-weight:400"><i></i><span><em>Latest</em> News</span></h2>
  <div class="abs card-icon"><svg width="34" height="30" viewBox="0 0 34 30"><path d="M4 10h8l14-8v26l-14-8H4z" fill="#333"/><rect x="8" y="20" width="5" height="8" fill="#333"/></svg></div>
  <p class="abs card-text" style="letter-spacing:0"><span class="news-head">Kauitm veleum iriure lorrfu</span><br>Hdrehrit in vulptate velit essehi molestie coequa. molestie uitmi veleum iriure lorrfu hdrehrit</p>
  <a class="abs read-more">READ MORE »</a>
</article>

<div class="abs divider"></div>

<section>
  <h2 class="abs testi-title" style="font-weight:400"><em>Client</em><br>Testimonials</h2>
  <svg class="abs" style="left:281px;top:718px" width="34" height="80" viewBox="0 0 34 80"><path d="M0 0l32 40L0 80h6L34 40 6 0z" fill="#d8dcdb"/><path d="M0 0l32 40L0 80z" fill="#e6e9e8"/></svg>
  <p class="abs testi-quote"><span style="font-family:'Tinos',serif;font-size:30px;color:#aaa;line-height:0;vertical-align:-8px">“</span> Lorem ipsum sit amet consectet uradi incididunt ut labore et dolore magna aliquaps enimi ad minim veniam quiidunt ut labore etpvloore magn incididunt ut labore et dolore na aliquatmp enimt ad minim veniam quiidunt ut labore <span style="font-family:'Tinos',serif;font-size:30px;color:#aaa;line-height:0;vertical-align:-14px">”</span></p>
  <p class="abs testi-name">Mr. Dolore na Aliqua</p>
</section>

<footer class="abs site-footer">
  <h3 class="abs foot-h" style="left:133px;width:365px">Contact Info</h3>
  <svg class="abs" style="left:133px;top:58px" width="12" height="16" viewBox="0 0 12 16"><path d="M6 0a6 6 0 0 0-6 6c0 4 6 10 6 10s6-6 6-10a6 6 0 0 0-6-6z" fill="#c9d5e6"/><circle cx="6" cy="6" r="2" fill="#1f4e8c"/></svg>
  <p class="abs foot-text" style="left:156px;top:55px">Suite 1804 Harbourline<br>Tower<br>12 - 18 Kensington Road East<br>Eastbank, Hong Kong</p>
  <svg class="abs" style="left:338px;top:56px" width="10" height="16" viewBox="0 0 10 16"><rect x="0.5" y="0.5" width="9" height="15" rx="1.5" fill="none" stroke="#c9d5e6"/><rect x="2" y="2.5" width="6" height="8" fill="#c9d5e6"/></svg>
  <p class="abs foot-strong" style="left:365px;top:55px">469-555-0148</p>
  <svg class="abs" style="left:337px;top:92px" width="14" height="10" viewBox="0 0 14 10"><rect width="14" height="10" fill="#c9d5e6"/><path d="M0 0l7 6 7-6" fill="none" stroke="#1f4e8c"/></svg>
  <p class="abs foot-strong" style="left:365px;top:88px;font-size:13px">info@torvelcapital.com</p>

  <h3 class="abs foot-h" style="left:554px;width:241px">Newsletter Signup</h3>
  <div class="abs email-input">Enter your email</div>
  <div class="abs go-btn">GO</div>
  <div class="abs follow">Follow Us On: <i></i><i></i><i></i><i></i></div>

  <p class="abs copyright">© Copyright 2014 Torvel Capital.<br>All Rights Reserved</p>
</footer>
<div class="abs foot-badge"></div>
</body>
</html>
```